Business Cards for Branding (Advertising) Agency

We need stylish and cool business cards.
Additional info:
1) Logo - see the attachment. You can use either the three penguins or just one penguin face (square or round) - at your discretion.
2) Text and other stuff for business card:
front side:
-Logo and company name: company name - Northern Walruses - should be in English as is in logo. This is the only exception. The rest of the text will be in Russian.
-Who we are: Брендинговое агентство
-First and last name:
-Position: Управляющий партнёр
-Address:
-Phone:
-Email:
-Website:
Note: please don't use names of information fields, such as: who we are, first and last name, position, address, phone, email and website.

3) Our suggestions on design:
-The backside of the business card can be either blank or has something on it - at your discretion.
-The business card background should be either white or grey (you can use any tone of grey).

Additional Information:
1) БРЕНДИНГОВОЕ АГЕНТСТВО
2) ул. Кедровская - these two words should be together on the same line
3) тел.: +7 (495) 381-96-02
моб.: +7 (916) 507-28-94

```html
<!DOCTYPE html>
<html lang="ru">
<head>
<meta charset="utf-8">
<title>Northern Walruses — визитная карточка</title>
<link rel="stylesheet" href="https://fonts.googleapis.com/css2?family=PT+Serif:wght@400&family=Lato:wght@400;700&display=swap">
<style>
  :root {
    --page-bg: #2b2b2b;
    --card-bg: #ffffff;
    --ink: #1a1a1a;
    --ink-soft: #333333;
    --band: #0d0d0d;
    --band-text: #f2f2f2;
    --accent: #f2a51e;
    --accent-light: #f7c35a;
    --mascot-dark: #1c1c1c;
    --mascot-light: #8e8e8e;
  }
  * { box-sizing: border-box; margin: 0; padding: 0; }
  html, body {
    width: 1200px; height: 871px; overflow: hidden;
    background: var(--page-bg);
  }
  .business-card {
    position: absolute;
    left: 240px;
    width: 720px; height: 400px;
    background: var(--card-bg);
    overflow: hidden;
  }
  .business-card--back { top: 25px; }
  .business-card--front { top: 446px; }

  .back-mark {
    position: absolute; left: 265px; top: 110px;
    width: 190px; height: 170px; border-radius: 85px;
    background: linear-gradient(160deg, var(--mascot-light) 0%, var(--mascot-dark) 45%);
  }

  .holder {
    position: absolute; right: 44px; top: 26px;
    text-align: right;
  }
  .holder__name {
    font-family: "PT Serif", serif;
    font-size: 24px; line-height: 30px; color: var(--ink);
  }
  .holder__role {
    font-family: "PT Serif", serif;
    font-size: 13px; line-height: 18px; color: var(--ink-soft); margin-top: 2px;
  }
  .brand {
    position: absolute; left: 50px; top: 56px;
  }
  .brand__mascots {
    width: 130px; height: 62px; border-radius: 31px;
    background: linear-gradient(135deg, var(--mascot-dark), var(--mascot-light));
  }
  .brand__name {
    font-family: "Lato", sans-serif; font-weight: 700;
    font-size: 17px; line-height: 22px; letter-spacing: 1px; color: var(--ink);
    margin-top: 6px; text-transform: uppercase;
  }
  .agency {
    position: absolute; left: 50px; top: 176px;
    font-family: "PT Serif", serif; font-size: 23px; line-height: 30px; color: var(--ink);
  }
  .contacts {
    position: absolute; left: 50px; top: 216px;
    font-family: "Lato", sans-serif; font-size: 16px;
    line-height: 22px; color: var(--ink);
    list-style: none;
  }
  .swoosh {
    position: absolute; left: 0; bottom: 0; width: 720px; height: 144px;
  }
  .address {
    position: absolute; left: 50px; bottom: 20px;
    font-family: "PT Serif", serif; font-size: 17px; line-height: 22px;
    letter-spacing: 0.4px; color: var(--band-text);
  }
  .mascot {
    position: absolute; right: 36px; top: 104px;
    width: 180px; height: 216px; border-radius: 86px 86px 80px 80px;
    background: linear-gradient(160deg, var(--mascot-light) 0%, var(--mascot-dark) 45%);
  }
</style>
</head>
<body>
  <section class="business-card business-card--back" aria-label="Оборотная сторона">
    <div class="back-mark" role="img" aria-label="Иллюстрация: мультяшный персонаж-талисман агентства в шапке-ушанке"></div>
  </section>

  <article class="business-card business-card--front">
    <header class="holder">
      <p class="holder__name">Мария Соколова</p>
      <p class="holder__role">Управляющий партнёр</p>
    </header>

    <div class="brand">
      <div class="brand__mascots" role="img" aria-label="Иллюстрация: три мультяшных персонажа-талисмана агентства"></div>
      <p class="brand__name">Northern Walruses</p>
    </div>

    <p class="agency">Брендинговое агентство</p>

    <ul class="contacts">
      <li>+7 (916) 507-28-94</li>
      <li>maria@northernwalruses.ru</li>
      <li>www.northernwalruses.ru</li>
    </ul>

    <svg class="swoosh" viewBox="0 0 720 144" aria-hidden="true">
      <path d="M0 68 C 187 50, 403 29, 720 22 L 720 144 L 0 144 Z" fill="var(--accent-light)"/>
      <path d="M0 76 C 202 59, 418 42, 720 37 L 720 144 L 0 144 Z" fill="var(--accent)"/>
      <path d="M0 85 C 216 71, 432 58, 720 56 L 720 144 L 0 144 Z" fill="var(--card-bg)"/>
      <path d="M0 79 C 230 92, 461 86, 720 63 L 720 144 L 0 144 Z" fill="var(--band)"/>
    </svg>

    <div class="mascot" role="img" aria-label="Иллюстрация: мультяшный персонаж-талисман в шапке-ушанке машет крылом"></div>

    <p class="address">115230, г. Москва, ул. Кедровская, д.12, стр.2</p>
  </article>
</body>
</html>
```